One of a kind service business!

We are the only ocean freight auditing company in the entire world that does what we do. We provide a innovative service in auditing our clients invoices for billing errors as it relates to the import and export of their products anywhere in the world. We'd like to retain the current logo - but we are open to any interesting concepts that can complete the card.

Target Market(s)

C-Level and Senior Financial executives

Industry/Entity Type

Auditing

Requirements
Must have

• ONE SIDED ONLY
Should not have
• no cartoonish images

```html
<!DOCTYPE html>
<html lang="en">
<head>
<meta charset="utf-8">
<title>Bluewake Review – Business Card</title>
<link rel="stylesheet" href="https://fonts.googleapis.com/css2?family=Arimo:wght@400;700&display=swap">
<style>
  :root {
    --page-bg: #e6e6e6;
    --card-bg: #ffffff;
    --ocean-blue: #0a77ad;
    --brand-blue: #1b6ea6;
    --leaf-green: #8dc63f;
    --ink: #1f1f1f;
    --white: #ffffff;
  }
  * { margin: 0; padding: 0; box-sizing: border-box; }
  html, body {
    width: 1200px;
    height: 944px;
    overflow: hidden;
    background: var(--page-bg);
    font-family: "Arimo", Arial, sans-serif;
  }
  .business-card {
    position: absolute;
    left: 98px;
    top: 184px;
    width: 1003px;
    height: 576px;
    border-radius: 28px;
    overflow: hidden;
    background: var(--card-bg);
  }
  .wave-panel {
    position: absolute;
    inset: 0;
    width: 100%;
    height: 100%;
  }
  .wave-green { fill: var(--leaf-green); }
  .wave-blue { fill: var(--ocean-blue); }

  .brand {
    position: absolute;
    left: 62px;
    top: 78px;
    display: flex;
    align-items: center;
    gap: 14px;
  }
  .brand-mark {
    width: 22px;
    height: 22px;
    background: var(--brand-blue);
  }
  .brand-name {
    font-weight: 700;
    font-size: 50px;
    line-height: 1;
    color: var(--brand-blue);
  }

  .contact-list {
    position: absolute;
    left: 80px;
    top: 0;
    list-style: none;
    color: var(--ink);
    font-size: 27px;
    line-height: 34px;
  }
  .contact-item {
    position: absolute;
    left: 0;
    display: flex;
    align-items: flex-start;
    white-space: nowrap;
  }
  .contact-icon {
    width: 22px;
    height: 22px;
    margin-top: 6px;
    margin-right: 12px;
    flex: none;
    fill: var(--ocean-blue);
  }
  .address { top: 236px; }
  .phone-main { top: 338px; }
  .phone-mobile { top: 372px; }
  .fax { top: 406px; }
  .website { top: 440px; }
  .email { top: 474px; }

  .person {
    position: absolute;
    left: 640px;
    top: 432px;
    width: 340px;
    text-align: center;
    color: var(--white);
  }
  .person-name {
    font-size: 37px;
    font-weight: 400;
    line-height: 44px;
  }
  .person-title {
    font-size: 25px;
    line-height: 32px;
  }
</style>
</head>
<body>
  <article class="business-card">
    <svg class="wave-panel" viewBox="0 0 1003 576" preserveAspectRatio="none" aria-hidden="true">
      <path class="wave-green" d="M617 0 C580 110 600 240 565 340 C535 430 508 500 508 576 L1003 576 L1003 0 Z"/>
      <path class="wave-blue" d="M728 0 C695 110 705 220 668 330 C640 420 612 480 605 576 L1003 576 L1003 0 Z"/>
    </svg>

    <div class="brand">
      <span class="brand-mark"></span>
      <span class="brand-name">Bluewake Review</span>
    </div>

    <ul class="contact-list">
      <li class="contact-item address">
        <svg class="contact-icon" viewBox="0 0 24 24"><path d="M12 2 L1 12 H4 V22 H10 V15 H14 V22 H20 V12 H23 Z"/></svg>
        <span>2710 NW 48th St. Suite 1120<br>Coral Bay, Florida 33190</span>
      </li>
      <li class="contact-item phone-main">
        <svg class="contact-icon" viewBox="0 0 24 24"><path d="M6.6 10.8c1.4 2.8 3.8 5.1 6.6 6.6l2.2-2.2c.3-.3.7-.4 1-.2 1.1.4 2.3.6 3.6.6.6 0 1 .4 1 1V20c0 .6-.4 1-1 1C10.6 21 3 13.4 3 4c0-.6.4-1 1-1h3.5c.6 0 1 .4 1 1 0 1.3.2 2.5.6 3.6.1.3 0 .7-.2 1z"/></svg>
        <span>+420.555.014.392</span>
      </li>
      <li class="contact-item phone-mobile">
        <svg class="contact-icon" viewBox="0 0 24 24"><path d="M6.6 10.8c1.4 2.8 3.8 5.1 6.6 6.6l2.2-2.2c.3-.3.7-.4 1-.2 1.1.4 2.3.6 3.6.6.6 0 1 .4 1 1V20c0 .6-.4 1-1 1C10.6 21 3 13.4 3 4c0-.6.4-1 1-1h3.5c.6 0 1 .4 1 1 0 1.3.2 2.5.6 3.6.1.3 0 .7-.2 1z"/></svg>
        <span>555.210.4870</span>
      </li>
      <li class="contact-item fax">
        <svg class="contact-icon" viewBox="0 0 24 24"><path d="M6 2h9l3 3v5H6z M2 11h20v10H2z M5 14v2h6v-2z"/></svg>
        <span>555.675.0193</span>
      </li>
      <li class="contact-item website">
        <svg class="contact-icon" viewBox="0 0 24 24"><path d="M12 2a10 10 0 1 0 0 20 10 10 0 0 0 0-20zm0 2c.9 1.2 1.6 2.8 2 4.5h-4c.4-1.7 1.1-3.3 2-4.5zM4.3 14a8 8 0 0 1 0-4h3.5a16 16 0 0 0 0 4zm.9 2h3c.4 1.6 1 3 1.8 4a8 8 0 0 1-4.8-4zm3-8h-3A8 8 0 0 1 10 4c-.8 1-1.4 2.4-1.8 4zM12 20c-.9-1.2-1.6-2.8-2-4h4c-.4 1.2-1.1 2.8-2 4zm2.3-6H9.7a14 14 0 0 1 0-4h4.6a14 14 0 0 1 0 4zm.5 6c.7-1 1.3-2.4 1.7-4h3a8 8 0 0 1-4.7 4zm1.4-6a16 16 0 0 0 0-4h3.5a8 8 0 0 1 0 4zm-.4-6c-.4-1.6-1-3-1.8-4a8 8 0 0 1 4.8 4z"/></svg>
        <span>www.bluewakereview.net</span>
      </li>
      <li class="contact-item email">
        <svg class="contact-icon" viewBox="0 0 24 24"><path d="M2 9 L12 3 L22 9 V21 H2 Z M4 10 L12 15 L20 10 L12 5 Z"/></svg>
        <span>danielm@bluewakereview.net</span>
      </li>
    </ul>

    <div class="person">
      <p class="person-name">Daniel Moreau</p>
      <p class="person-title">CEO</p>
    </div>
  </article>
</body>
</html>
```